Business Card Design Project

Business Card
We are rebranding with a new logo
Industry/Entity Type
Business
Contact Information for Business Card
Dennis Morvale +61 487215963 dennis@quorv.com.au P.O. Box 872 Fernlow QLD 4309
Requirements
Must have
- Logo

```html
<!DOCTYPE html>
<html lang="en">
<head>
<meta charset="utf-8">
<title>Quorv International – Business Card</title>
<link rel="stylesheet" href="https://fonts.googleapis.com/css2?family=Marcellus&family=Montserrat:wght@300;400&display=swap">
<style>
  :root {
    --page: #e6e6e6;
    --card-light: #f4f4f4;
    --card-light-shade: #d9d9d9;
    --card-dark: #2e3033;
    --card-dark-deep: #1f2123;
    --accent: #2a9fd8;
    --ink-light: #e4e6e8;
    --ink-dark: #3a3a3a;
    --tab: #3b3d40;
  }
  html, body {
    margin: 0;
    width: 1200px;
    height: 686px;
    overflow: hidden;
    background: var(--page);
  }
  .card {
    position: absolute;
    left: 75px;
    top: 43px;
    width: 1050px;
    height: 600px;
    box-shadow: 0 10px 30px rgba(0,0,0,0.25);
    overflow: hidden;
  }
  .card-art {
    position: absolute;
    inset: 0;
  }
  .brand {
    position: absolute;
    left: 60px;
    top: 210px;
    width: 280px;
    display: flex;
    align-items: center;
    gap: 14px;
  }
  .brand-mark {
    width: 22px;
    height: 22px;
    background: var(--accent);
    flex: none;
  }
  .brand-name {
    font-family: "Marcellus", serif;
    font-size: 30px;
    line-height: 1.05;
    color: var(--accent);
    letter-spacing: 1px;
  }
  .person {
    position: absolute;
    left: 0;
    top: 405px;
    width: 400px;
    text-align: center;
  }
  .person-name {
    font-family: "Marcellus", serif;
    font-size: 34px;
    color: var(--accent);
    margin: 0;
    letter-spacing: 0.5px;
  }
  .person-role {
    font-family: "Marcellus", serif;
    font-size: 18px;
    color: var(--ink-dark);
    margin: 4px 0 0;
    letter-spacing: 2px;
  }
  .contact {
    position: absolute;
    margin: 0;
    font-family: "Montserrat", sans-serif;
    font-weight: 300;
    font-size: 25px;
    letter-spacing: 2px;
    color: var(--ink-light);
    white-space: nowrap;
  }
  .contact-phone   { left: 445px; top: 94px; }
  .contact-email   { left: 465px; top: 214px; }
  .contact-web     { left: 485px; top: 334px; }
  .contact-address { left: 505px; top: 454px; font-size: 22px; }
  .tagline {
    position: absolute;
    left: 1016px;
    top: 60px;
    width: 28px;
    height: 200px;
    writing-mode: vertical-rl;
    text-align: center;
    font-family: "Montserrat", sans-serif;
    font-size: 11px;
    letter-spacing: 5px;
    color: var(--ink-light);
  }
</style>
</head>
<body>
<div class="card">
  <svg class="card-art" width="1050" height="600" viewBox="0 0 1050 600">
    <defs>
      <linearGradient id="lightPanel" x1="0" y1="0" x2="1" y2="1">
        <stop offset="0" stop-color="var(--card-light)"/>
        <stop offset="1" stop-color="var(--card-light-shade)"/>
      </linearGradient>
      <linearGradient id="cityPhoto" x1="0" y1="0" x2="1" y2="1">
        <stop offset="0" stop-color="var(--card-dark-deep)"/>
        <stop offset="0.5" stop-color="#3a3d41"/>
        <stop offset="1" stop-color="var(--card-dark)"/>
      </linearGradient>
    </defs>
    <rect class="panel-light" width="1050" height="600" fill="url(#lightPanel)"/>
    <g role="img" aria-label="Faint monochrome photograph of city towers">
      <polygon class="panel-dark" points="370,0 1050,0 1050,600 470,600" fill="url(#cityPhoto)"/>
    </g>
    <line class="edge-line" x1="362" y1="0" x2="462" y2="600" stroke="var(--accent)" stroke-width="5"/>
    <line class="side-line" x1="1008" y1="0" x2="1008" y2="600" stroke="var(--accent)" stroke-width="4"/>
    <polygon class="tagline-tab" points="1014,40 1046,60 1046,270 1014,290" fill="var(--tab)"/>

    <!-- phone -->
    <g transform="translate(388,110)">
      <polygon points="0,-24 21,-12 21,12 0,24 -21,12 -21,-12" fill="var(--accent)"/>
      <rect x="-7" y="-12" width="14" height="24" rx="2" fill="none" stroke="#fff" stroke-width="2"/>
      <circle cx="0" cy="8" r="1.5" fill="#fff"/>
    </g>
    <!-- email -->
    <g transform="translate(408,230)">
      <polygon points="0,-24 21,-12 21,12 0,24 -21,12 -21,-12" fill="var(--accent)"/>
      <rect x="-11" y="-7" width="22" height="14" fill="#fff"/>
      <polyline points="-11,-7 0,2 11,-7" fill="none" stroke="var(--accent)" stroke-width="1.6"/>
    </g>
    <!-- web -->
    <g transform="translate(428,350)">
      <polygon points="0,-24 21,-12 21,12 0,24 -21,12 -21,-12" fill="var(--accent)"/>
      <circle r="10" fill="none" stroke="#fff" stroke-width="1.8"/>
      <ellipse rx="4.5" ry="10" fill="none" stroke="#fff" stroke-width="1.4"/>
      <line x1="-10" y1="0" x2="10" y2="0" stroke="#fff" stroke-width="1.4"/>
    </g>
    <!-- pin -->
    <g transform="translate(448,470)">
      <polygon points="0,-24 21,-12 21,12 0,24 -21,12 -21,-12" fill="var(--accent)"/>
      <path d="M0,12 C-4,5 -9,0 -9,-4 A9,9 0 0 1 9,-4 C9,0 4,5 0,12 Z" fill="#fff"/>
      <circle cx="0" cy="-4" r="3.5" fill="var(--accent)"/>
    </g>
  </svg>

  <div class="brand">
    <span class="brand-mark"></span>
    <span class="brand-name">QUORV<br>INTERNATIONAL</span>
  </div>

  <div class="person">
    <p class="person-name">Dennis Morvale</p>
    <p class="person-role">C.E.O</p>
  </div>

  <p class="contact contact-phone">+61 487215963</p>
  <p class="contact contact-email">dennis@quorv.com.au</p>
  <p class="contact contact-web">www.quorv.com.au</p>
  <p class="contact contact-address">P.O. Box 872 Fernlow QLD 4309</p>

  <div class="tagline">WE DESIGN BEST</div>
</div>
</body>
</html>
```